Investment Memorandum Document

IM for Harbourline Lending Fund - is the document that needs work

Make sure it is all done in MS WORD so that i or lawyers can edit some words if required

the IM is NOT final but its 95% of the way there. Maybe a few more pages and wording changes - but that is something i can do i guess or you can easier adjust

Just to typeset and pretty it all up - a few sample finished products have been uploaded for reference.

KTR IM is the one i like - but feel free to show off your skills

put 1.2 to 1.8 all in contrasting row tables

Target Market(s)

Individual and Institutional investors with money

Industry/Entity Type

Investment Banking

Colors

Designer to choose colors to be used in the design.

Requirements
Must have
• clear professional layout and easy on the eye
• https://www.filevaultexample.net/sh/84k3p77zrm2wqtn/BBDfpqWem3PvtsLxQZMUD41Lb?dl=0
• use the link above for high res images
Nice to have
• pictures and graphics
Should not have
• cartoons

```html
<!DOCTYPE html>
<html lang="en">
<head>
<meta charset="utf-8">
<title>IM for Harbourline Lending Fund</title>
<link rel="stylesheet" href="https://fonts.googleapis.com/css2?family=Raleway:wght@400;500;600&family=Open+Sans:wght@400;600&display=swap">
<style>
:root{
  --bg:#ededed;
  --band:#b9b9b9;
  --band-dark:#8f8f8f;
  --paper:#ffffff;
  --gold:#c9963a;
  --ink:#6a6a6a;
  --ink-soft:#9a9a9a;
  --rule:#dedede;
  --sky-a:#9fb4c8;
  --sky-b:#4d6278;
}
*{box-sizing:border-box;margin:0;padding:0}
html,body{width:691px;height:1200px;overflow:hidden}
body{background:var(--bg);font-family:"Open Sans",sans-serif;color:var(--ink);position:relative}
.backdrop{position:absolute;inset:0;z-index:0}
.spread{position:absolute;left:28px;top:22px;display:grid;grid-template-columns:repeat(5,124px);grid-auto-rows:160px;column-gap:5px;row-gap:7px;z-index:1}
.page{background:var(--paper);box-shadow:0 1px 3px rgba(0,0,0,.18);position:relative;padding:9px 8px 12px;overflow:hidden}
.pg-foot{position:absolute;left:8px;right:8px;bottom:4px;border-top:.4px solid var(--rule);padding-top:1.5px;font-size:2px;color:var(--ink-soft);background:var(--paper)}
.pg-title{font-family:"Raleway",sans-serif;font-size:5.2px;color:var(--ink);font-weight:500;margin-bottom:3px;display:flex;align-items:center;gap:3px}
.pg-title.caps{text-transform:uppercase;color:var(--gold);font-size:4.4px}
.num{display:inline-block;background:var(--gold);color:#fff;min-width:8px;height:9px;font-size:5px;text-align:center;line-height:9px;padding:0 1px}
.sub{font-family:"Raleway",sans-serif;font-size:3.2px;color:var(--gold);font-weight:600;margin:2.5px 0 1.2px}
.txt p{font-size:2.2px;line-height:1.45;margin-bottom:1.4px;color:var(--ink);text-align:justify}
.cols{columns:2;column-gap:5px}
.photo.city{background:linear-gradient(160deg,var(--sky-a),var(--sky-b))}
.photo.warm{background:linear-gradient(160deg,#d9c7a6,#6c6a70)}
.photo.desk{background:linear-gradient(160deg,#e5e8ec,#8e9aa6)}
.tbl{width:100%;border-collapse:collapse;margin:2px 0}
.tbl td{font-size:2.1px;padding:1.2px 1.5px;vertical-align:top;line-height:1.4}
.tbl tr:nth-child(odd) td{background:#f4f1ea}
.tbl td:first-child{color:var(--gold);font-weight:600;width:30%}
.callout{background:var(--gold);color:#fff;font-family:"Raleway",sans-serif;font-size:3.2px;padding:4px;line-height:1.35;margin:3px 0}
.cover-brand{display:flex;align-items:center;gap:3px;margin:6px 0 0 30px;font-family:"Raleway",sans-serif;font-size:5px;color:var(--ink);white-space:nowrap}
.mark{width:5px;height:5px;background:var(--gold);flex:none}
.cover-title{font-family:"Raleway",sans-serif;color:var(--gold);font-size:4.6px;margin-top:14px}
.cover-sub{font-family:"Raleway",sans-serif;font-size:3.6px;margin-top:2px}
.cover-meta{font-size:2.2px;margin-top:10px;line-height:1.6}
.toc-row{display:flex;justify-content:space-between;font-size:2.3px;border-bottom:.4px solid var(--rule);padding:1.2px 0}
.flow{display:flex;justify-content:space-around;margin:3px 0}
.flow span{font-size:2px;border:.5px solid var(--gold);padding:1.5px 2px;background:#faf6ee}
.stat{font-family:"Raleway",sans-serif;color:var(--gold);font-size:9px}
.signoff{position:absolute;left:330px;top:1040px;width:300px;text-align:center;z-index:1}
.signoff .brand{display:flex;justify-content:center;align-items:center;gap:8px;font-family:"Raleway",sans-serif;color:#fff;font-size:20px;font-weight:500;letter-spacing:1px}
.signoff .brand .mark{width:16px;height:16px;background:#fff}
.signoff .im-line{font-family:"Raleway",sans-serif;color:#fff;font-size:13px;margin-top:34px}
</style>
</head>
<body>
<svg class="backdrop" width="691" height="1200" viewBox="0 0 691 1200" aria-hidden="true">
  <polygon points="691,360 691,1200 0,1200 0,1010" fill="var(--band)"/>
  <polygon points="691,560 691,1200 0,1200 0,1160" fill="var(--band-dark)"/>
</svg>

<main class="spread">
  <!-- Row 1 -->
  <section class="page">
    <div class="cover-brand"><span class="mark"></span>Halverton Asset Management</div>
    <div class="cover-title">Harbourline Lending Fund</div>
    <div class="cover-sub">Information Memorandum</div>
    <div class="cover-meta">Investment Manager<br>Halverton Asset Management Pty Ltd<br>Trustee<br>Harbourline Trustee Services Pty Ltd</div>
    <div class="photo city" style="position:absolute;left:0;right:0;bottom:0;height:66px" role="img" aria-label="City skyline and light trails at dusk"></div>
  </section>
  <section class="page" style="padding:0">
    <div class="photo city" style="height:70px" role="img" aria-label="Office towers viewed from below"></div>
    <div style="padding:5px 8px">
      <div class="pg-title caps">Table of Content</div>
      <div class="toc-row"><span>Message from the Managing Director</span><span>6</span></div>
      <div class="toc-row"><span>The Fund</span><span>7</span></div>
      <div class="toc-row"><span>The Loans</span><span>11</span></div>
      <div class="toc-row"><span>Risks</span><span>13</span></div>
      <div class="toc-row"><span>Fees and Costs</span><span>16</span></div>
      <div class="toc-row"><span>Management of the Fund</span><span>19</span></div>
      <div class="toc-row"><span>Taxation Information</span><span>21</span></div>
      <div class="toc-row"><span>Additional Information</span><span>22</span></div>
      <div class="toc-row"><span>Application Process</span><span>25</span></div>
      <div class="toc-row"><span>Glossary</span><span>26</span></div>
      <div class="toc-row"><span>Corporate Directory</span><span>28</span></div>
    </div>
  </section>
  <section class="page">
    <div class="pg-title caps">Important Notice</div>
    <div class="txt cols">
      <p>This memorandum has been prepared for general information only and is not a product disclosure statement. It has not been lodged with any regulator and the offer is open only to wholesale or sophisticated investors.</p>
      <p>Investors should read this memorandum in full and consider their own objectives, financial situation and needs before applying for units in the Fund.</p>
      <p>Neither the Trustee nor the Manager guarantees the repayment of capital, the payment of income or any particular rate of return. Past performance is not a reliable indicator of future results.</p>
      <p>The Fund offers investors exposure to short term commercial loans, each secured by a registered first mortgage over real property and assessed by the Manager before any advance is made.</p>
      <p>No person is authorised to give any information or make any representation about the offer that is not contained in this memorandum, and any such information may not be relied upon.</p>
      <p>The distribution of this memorandum outside Australia may be restricted by law, and persons who receive it outside Australia should seek advice on and observe any such restrictions.</p>
      <p>Applications will only be accepted on the form attached to this memorandum, and the Trustee may refuse any application at its discretion without giving reasons.</p>
      <p>Interest received from borrowers is pooled and distributed to unitholders monthly in arrears after the payment of Fund expenses and any provisions set aside for arrears.</p>
    </div>
    <div class="pg-foot">Page 3 · Harbourline Lending Fund · Information Memorandum</div>
  </section>
  <section class="page">
    <div class="pg-title caps">Important Notice</div>
    <div class="txt cols">
      <p>Neither the Trustee nor the Manager guarantees the repayment of capital, the payment of income or any particular rate of return on an investment in the Fund.</p>
      <p>Investors should read this memorandum in full and consider their own objectives, financial situation and needs before applying for units.</p>
      <div class="sub">No cooling off rights</div>
      <p>Cooling off rights do not apply to an investment in the Fund. Once an application has been accepted it cannot be withdrawn by the investor.</p>
      <p>The Trustee may vary the terms of the offer by notice to investors, provided the change is not materially adverse to their interests.</p>
      <div class="sub">Forward looking statements</div>
      <p>Some statements in this memorandum are forward looking. They reflect the current views of the Manager and are subject to risks and uncertainties beyond its control.</p>
      <p>Actual outcomes may differ materially from those expressed or implied, and investors should not place undue reliance on such statements.</p>
      <p>Examples and figures used are for illustration only and do not represent a forecast of the returns of the Fund.</p>
    </div>
    <div class="pg-foot">Page 4 · Harbourline Lending Fund · Information Memorandum</div>
  </section>
  <section class="page">
    <div class="pg-title caps">Important Notice</div>
    <div class="txt cols">
      <p>This memorandum is dated on the date shown on the cover and the information in it is current only at that date unless stated otherwise.</p>
      <p>The Manager may update information that is not materially adverse by posting notice on its website and providing copies on request.</p>
      <div class="sub">Privacy</div>
      <p>By applying for units, investors consent to the collection and use of their personal information for the purpose of administering their investment in the Fund.</p>
      <p>Information may be disclosed to service providers, auditors and regulators where required by law.</p>
      <div class="sub">Currency</div>
      <p>All amounts are in Australian dollars unless stated otherwise and all times refer to Melbourne time.</p>
      <div class="sub">Photographs</div>
      <p>Photographs used in this memorandum are for illustration only and are not assets of the Fund unless stated.</p>
      <p>Defined terms used throughout are explained in the glossary at the end of this memorandum.</p>
    </div>
    <div class="pg-foot">Page 5 · Harbourline Lending Fund · Information Memorandum</div>
  </section>

  <!-- Row 2 -->
  <section class="page">
    <div class="pg-title">Message from the Managing Director</div>
    <div class="txt">
      <p>Dear Investor,</p>
      <p>On behalf of Halverton Asset Management it is my pleasure to invite you to invest in the Harbourline Lending Fund, a fund built to deliver regular monthly income secured by quality commercial property.</p>
      <p>Our team has originated and managed commercial loans through several property cycles. Every loan is assessed on its valuation, the strength of the borrower and a clear exit strategy before any Fund monies are advanced.</p>
      <p>The Fund gives investors access to a portfolio of short term first mortgage loans that would otherwise be difficult to reach, with transparent reporting on each loan and the security that supports it.</p>
      <p>We believe the Fund offers an attractive balance of income and capital protection, and we look forward to welcoming you as an investor.</p>
      <p>I encourage you to read this memorandum in full and to seek independent advice before making a decision to invest.</p>
      <p>Yours faithfully,<br>Managing Director<br>Halverton Asset Management Pty Ltd</p>
    </div>
    <div class="pg-foot">Page 6 · Harbourline Lending Fund · Information Memorandum</div>
  </section>
  <section class="page">
    <div class="pg-title"><span class="num">1</span>The Fund</div>
    <div class="sub">1.1 Fund Outline</div>
    <div class="txt"><p>The Fund is an unregistered managed investment scheme that offers wholesale investors exposure to secured short term commercial loans originated and managed by Halverton.</p></div>
    <div class="flow"><span>Investors</span><span>Trustee</span><span>Manager</span></div>
    <div class="flow"><span>Loan A</span><span>Loan B</span><span>Loan C</span></div>
    <div class="txt">
      <p>Investor monies are held by the Trustee and advanced to borrowers once the Manager has approved each loan. Loans are secured by registered first mortgages over commercial property.</p>
      <p>Interest received is pooled and distributed monthly to unitholders after expenses. Each investor holds units in the Fund rather than a direct interest in any single loan.</p>
      <p>The Manager monitors every loan monthly and reports on arrears, valuations and repayments in its quarterly investor report.</p>
    </div>
    <div class="pg-foot">Page 7 · Harbourline Lending Fund · Information Memorandum</div>
  </section>
  <section class="page">
    <div class="sub">1.2 Key Features</div>
    <table class="tbl">
      <tr><td>Trustee</td><td>Harbourline Trustee Services Pty Ltd, responsible for holding Fund assets and acting in the best interests of unitholders</td></tr>
      <tr><td>Manager</td><td>Halverton Asset Management Pty Ltd, responsible for originating, assessing and managing each loan</td></tr>
      <tr><td>Structure</td><td>Unregistered unit trust open to wholesale investors only</td></tr>
      <tr><td>Investment</td><td>Secured first mortgage commercial loans with conservative loan to value ratios</td></tr>
      <tr><td>Term</td><td>Twelve to thirty six months per loan, with options to extend at the Manager's discretion</td></tr>
      <tr><td>Who can invest</td><td>Wholesale and sophisticated investors who meet the legal tests</td></tr>
      <tr><td>Security</td><td>Registered first mortgage and guarantees from directors</td></tr>
      <tr><td>Reporting</td><td>Quarterly investor reports and annual audited accounts</td></tr>
    </table>
    <div class="pg-foot">Page 8 · Harbourline Lending Fund · Information Memorandum</div>
  </section>
  <section class="page">
    <table class="tbl">
      <tr><td>Target returns</td><td>Monthly income paid from interest received on loans</td></tr>
      <tr><td>Minimum</td><td>Fifty thousand dollars per application</td></tr>
      <tr><td>Distributions</td><td>Paid monthly in arrears to a nominated account</td></tr>
      <tr><td>Withdrawal</td><td>At loan maturity, subject to available liquidity</td></tr>
    </table>
    <div class="sub">1.3 Fund Units</div>
    <div class="txt">
      <p>Units are issued at one dollar each and carry equal rights to income and capital. The Trustee keeps a register of all unitholders and issues a statement after each application.</p>
      <p>Units are not quoted on any exchange and there is no established market for them. Investors should be prepared to hold units until the loans they fund are repaid.</p>
      <p>The Trustee may issue units in separate classes linked to individual loans, each with its own rate of return and term as set out in the relevant offer supplement.</p>
    </div>
    <div class="pg-foot">Page 9 · Harbourline Lending Fund · Information Memorandum</div>
  </section>
  <section class="page">
    <div class="sub">1.4 Distributions</div>
    <div class="txt">
      <p>Interest received from borrowers is pooled and distributed to unitholders monthly in arrears, after the payment of Fund expenses and any provisions for arrears.</p>
      <p>Distributions are paid by electronic transfer to the account nominated on the application form within ten business days after the end of each month.</p>
      <p>Where a borrower is late in paying interest, the Manager may defer the related distribution until the interest is received.</p>
    </div>
    <div class="sub">1.5 Withdrawal rights</div>
    <div class="txt">
      <p>Investors do not have a right to withdraw before the loan they fund is repaid. Capital is returned when the borrower repays the loan in full.</p>
      <p>The Trustee may, at its discretion, accept an early withdrawal request where another investor is able to take up the units.</p>
      <p>Where a loan is extended, investors will be notified and may elect to remain invested or exit on repayment.</p>
    </div>
    <div class="pg-foot">Page 10 · Harbourline Lending Fund · Information Memorandum</div>
  </section>

  <!-- Row 3 -->
  <section class="page">
    <div class="sub">1.6 Transfer of Units</div>
    <div class="txt"><p>Units may be transferred with the consent of the Trustee, which will not be unreasonably withheld. Transfers must be to a person who is a wholesale investor and must be made on the standard form.</p><p>Stamp duty or other costs of transfer are payable by the transferring parties.</p></div>
    <div class="sub">1.7 Borrowings</div>
    <div class="txt"><p>The Fund does not intend to borrow. Any future borrowing would be limited and disclosed to investors in advance.</p></div>
    <div class="sub">1.8 Other</div>
    <div class="txt"><p>The Trustee may close the Fund to new applications at any time and may wind up the Fund in accordance with the trust deed.</p></div>
    <div class="photo city" style="height:34px;margin-top:3px" role="img" aria-label="Elevated highway through the city at night"></div>
    <div class="pg-foot">Page 11 · Harbourline Lending Fund · Information Memorandum</div>
  </section>
  <section class="page">
    <div class="pg-title"><span class="num">2</span>The Loan Investments</div>
    <div class="sub">2.1 Lending strategy</div>
    <div class="txt"><p>The Fund lends to experienced borrowers against completed commercial property, land with approvals and selected construction projects. Loans are short term and secured by registered first mortgages.</p></div>
    <div class="sub">2.2 Investment criteria</div>
    <div class="txt"><p>Each loan is assessed for the value of the security, the borrower's experience and financial strength, and a clear strategy for repayment through sale or refinance.</p><p>The maximum loan to value ratio is set conservatively and the Manager will not lend on speculative property.</p></div>
    <div class="sub">2.3 Valuation policy</div>
    <div class="txt"><p>An independent valuation is obtained from a panel valuer before settlement and is reviewed whenever the Manager considers the value of the security may have changed.</p></div>
    <div class="pg-foot">Page 12 · Harbourline Lending Fund · Information Memorandum</div>
  </section>
  <section class="page">
    <div class="sub">2.4 Documentation and security</div>
    <div class="txt"><p>All loans are documented by the Fund's solicitors on standard terms. Security includes a registered first mortgage, guarantees from directors and, where relevant, a charge over the borrowing entity.</p><p>Title insurance and building insurance are required on every security property.</p></div>
    <div class="sub">2.5 Default management</div>
    <div class="txt"><p>Where a borrower is in default, the Manager will act promptly to enforce the security, which may include appointing a receiver and selling the property to recover the outstanding loan, interest and costs.</p></div>
    <div class="sub">2.6 Investing surplus funds</div>
    <div class="txt"><p>Monies awaiting deployment are held in an interest bearing account with an Australian bank until a loan is settled or capital is returned to investors.</p></div>
    <div class="pg-foot">Page 13 · Harbourline Lending Fund · Information Memorandum</div>
  </section>
  <section class="page" style="padding-top:0">
    <div class="photo city" style="height:52px;margin:0 -8px" role="img" aria-label="Financial district towers under cloudy sky"></div>
    <div class="pg-title" style="margin-top:4px"><span class="num">3</span>Risks</div>
    <div class="txt">
      <p>Like any investment, an investment in the Fund carries risk and investors may lose some or all of their capital. The key risks are summarised below, although the list is not exhaustive.</p>
      <p>Investors should consider these risks carefully, together with their own circumstances, and seek independent advice before applying.</p>
      <p>The Manager applies disciplined lending criteria to reduce these risks, but cannot remove them entirely and does not guarantee any return.</p>
      <p>Risks may change over time as market conditions and the composition of the loan portfolio change.</p>
    </div>
    <div class="pg-foot">Page 14 · Harbourline Lending Fund · Information Memorandum</div>
  </section>
  <section class="page">
    <div class="sub">Borrower default risk</div>
    <div class="txt"><p>A borrower may fail to pay interest or repay the loan on time. Recovery through sale of the security may take time and may not cover the full amount owed.</p></div>
    <div class="sub">Concentration risk</div>
    <div class="txt"><p>Where units are linked to a single loan, returns depend entirely on that borrower and that property, rather than a spread of loans.</p></div>
    <div class="sub">Development risk</div>
    <div class="txt"><p>Construction loans are exposed to cost overruns, delays and builder failure, which may reduce the value of the security.</p></div>
    <div class="sub">Liquidity risk</div>
    <div class="txt"><p>Withdrawals depend on loan repayments, and investors may be unable to exit before a loan is repaid.</p></div>
    <div class="sub">Market risk</div>
    <div class="txt"><p>A fall in property values may reduce the proceeds available on sale of the security.</p></div>
    <div class="pg-foot">Page 15 · Harbourline Lending Fund · Information Memorandum</div>
  </section>

  <!-- Row 4 -->
  <section class="page">
    <div class="sub">Documentation risk</div>
    <div class="txt"><p>A deficiency in loan or security documents may delay or limit recovery. The Manager uses experienced solicitors to reduce this risk.</p></div>
    <div class="sub">Valuation risk</div>
    <div class="txt"><p>A valuation is an opinion at a point in time and the price achieved on sale may be lower than the valued amount.</p></div>
    <div class="sub">Operational risk</div>
    <div class="txt"><p>Errors, system failures or the loss of key staff at the Manager or Trustee may affect the administration of the Fund.</p></div>
    <div class="sub">Regulatory risk</div>
    <div class="txt"><p>Changes in law, tax or regulatory policy may affect the Fund, its borrowers or the returns paid to investors.</p></div>
    <div class="sub">Interest rate risk</div>
    <div class="txt"><p>Changes in market rates may affect borrower demand and the rates the Fund can achieve on new loans.</p></div>
    <div class="pg-foot">Page 16 · Harbourline Lending Fund · Information Memorandum</div>
  </section>
  <section class="page">
    <div class="sub">Related party risk</div>
    <div class="txt"><p>The Manager and its associates may have interests in transactions involving the Fund. Such transactions are conducted on arm's length terms and disclosed to the Trustee.</p><p>The Trustee monitors related party dealings under its conflicts policy.</p></div>
    <div class="callout">We strongly recommend that investors obtain independent financial advice before investing in the Fund.</div>
    <div class="txt"><p>The risks described in this section are not the only risks that may affect the Fund. Other risks, including general economic conditions, may also affect returns.</p><p>Investors should consider whether an investment in the Fund suits their circumstances and their tolerance for risk.</p></div>
    <div class="pg-foot">Page 17 · Harbourline Lending Fund · Information Memorandum</div>
  </section>
  <section class="page">
    <div class="pg-title"><span class="num">4</span>Fees and costs</div>
    <div class="sub">4.1 Fees and Costs</div>
    <div class="txt"><p>The table below summarises the fees and costs that may be charged to the Fund or to investors. Fees are expressed inclusive of GST.</p></div>
    <table class="tbl">
      <tr><td>Establishment</td><td>Nil</td></tr>
      <tr><td>Contribution fee</td><td>Nil</td></tr>
      <tr><td>Management fee</td><td>Paid by borrowers, not investors</td></tr>
      <tr><td>Trustee fee</td><td>Met from the loan margin</td></tr>
      <tr><td>Withdrawal fee</td><td>Nil</td></tr>
      <tr><td>Performance fee</td><td>Nil</td></tr>
      <tr><td>Expenses</td><td>Recovered from the Fund as incurred</td></tr>
    </table>
    <div class="txt"><p>Borrowers pay establishment and line fees to the Manager in addition to interest paid to the Fund.</p></div>
    <div class="pg-foot">Page 18 · Harbourline Lending Fund · Information Memorandum</div>
  </section>
  <section class="page">
    <div class="sub">4.2 Goods and services tax</div>
    <div class="txt"><p>All fees are quoted inclusive of GST less any reduced input tax credits that the Fund is entitled to claim.</p></div>
    <div class="sub">4.3 Waiver, deferral or rebate</div>
    <div class="txt"><p>The Manager may waive, defer or rebate any part of its fees at its discretion. Any rebate will not increase the fees paid by other investors.</p></div>
    <div class="sub">4.4 Adviser fees</div>
    <div class="txt"><p>Fees paid to a financial adviser are agreed between the investor and adviser.</p></div>
    <div class="photo desk" style="height:50px;margin-top:3px" role="img" aria-label="Hands working with a calculator and documents"></div>
    <div class="pg-foot">Page 19 · Harbourline Lending Fund · Information Memorandum</div>
  </section>
  <section class="page">
    <div class="pg-title"><span class="num">5</span>Northgate Investment Group</div>
    <div class="txt"><p>Northgate Investment Group has originated and managed commercial property loans for over two decades, working with developers, investors and business owners across the eastern states.</p></div>
    <div class="stat">$1.0 <span style="font-size:3px">billion</span></div>
    <div class="txt"><p>In loans settled since inception, with a strong record of capital returned to investors.</p></div>
    <div class="sub">Key management</div>
    <div class="txt"><p>The group's directors bring experience in banking, property development, law and credit, and are closely involved in the approval of every loan.</p><p>The credit committee meets weekly to review new applications and the performance of existing loans.</p></div>
    <div class="pg-foot">Page 20 · Harbourline Lending Fund · Information Memorandum</div>
  </section>

  <!-- Row 5 -->
  <section class="page">
    <div class="sub">Project Pipeline</div>
    <div class="pg-title">Wharfside Residences</div>
    <div class="txt"><p>A completed residential tower on the waterfront, funded through a senior construction facility and repaid in full on settlement of apartment sales.</p></div>
    <table class="tbl"><tr><td>Location</td><td>Docklands</td></tr><tr><td>Loan</td><td>Senior first mortgage</td></tr><tr><td>Status</td><td>Repaid in full</td></tr></table>
    <div class="photo city" style="height:68px;margin-top:3px" role="img" aria-label="Residential tower beside a waterfront"></div>
    <div class="pg-foot">Page 21 · Harbourline Lending Fund · Information Memorandum</div>
  </section>
  <section class="page">
    <div class="sub">Project Pipeline</div>
    <div class="pg-title">Queensbury Park Apartments</div>
    <div class="txt"><p>A boutique apartment building near the park, funded through a construction facility with a conservative loan to value ratio and staged drawdowns.</p></div>
    <table class="tbl"><tr><td>Location</td><td>Inner south</td></tr><tr><td>Loan</td><td>Construction facility</td></tr><tr><td>Status</td><td>Repaid in full</td></tr></table>
    <div class="photo warm" style="height:68px;margin-top:3px" role="img" aria-label="Modern apartment building with glass facade"></div>
    <div class="pg-foot">Page 22 · Harbourline Lending Fund · Information Memorandum</div>
  </section>
  <section class="page">
    <div class="pg-title"><span class="num">6</span>Management of the Fund</div>
    <div class="sub">6.1 About Halverton Asset Management</div>
    <div class="txt"><p>Halverton Asset Management Pty Ltd is the investment manager of the Fund. It is responsible for sourcing, assessing and managing loans and for reporting to the Trustee and investors.</p><p>Its team combines experience in credit, property and funds management, and it applies a documented lending policy to every transaction.</p></div>
    <div class="sub">6.2 The Trustee</div>
    <div class="txt"><p>Harbourline Trustee Services Pty Ltd acts as trustee of the Fund. It holds the Fund's assets on trust for unitholders and oversees the Manager's performance under the management agreement.</p><p>The Trustee maintains the unit register and arranges the annual audit of the Fund's accounts.</p></div>
    <div class="pg-foot">Page 23 · Harbourline Lending Fund · Information Memorandum</div>
  </section>
  <section class="page">
    <div class="pg-title"><span class="num">7</span>Taxation information</div>
    <div class="txt">
      <p>The taxation consequences of investing in the Fund depend on each investor's circumstances, and investors should seek professional tax advice before investing.</p>
      <p>The Fund intends to distribute all of its taxable income each year so that the Trustee is not taxed. Investors will be assessed on their share of that income whether or not it has been paid.</p>
      <p>An annual tax statement will be provided to each investor after the end of the financial year to assist with the preparation of tax returns.</p>
      <p>Investors who do not provide a tax file number or exemption may have tax withheld from distributions at the highest marginal rate.</p>
    </div>
    <div class="pg-foot">Page 24 · Harbourline Lending Fund · Information Memorandum</div>
  </section>
  <section class="page">
    <div class="pg-title"><span class="num">8</span>Additional Information</div>
    <div class="sub">8.1 Material documents</div>
    <div class="txt"><p>The following documents govern the Fund and are available to investors on request from the Manager free of charge.</p></div>
    <div class="sub">8.2 Trust Deed</div>
    <div class="txt"><p>The trust deed sets out the rights and obligations of the Trustee and investors, including the issue and redemption of units, meetings and the winding up of the Fund.</p></div>
    <div class="sub">8.3 Management Agreement</div>
    <div class="txt"><p>The management agreement appoints the Manager, sets out its duties and fees, and allows the Trustee to remove the Manager in certain circumstances.</p><p>The agreement continues until the Fund is wound up unless terminated earlier.</p></div>
    <div class="pg-foot">Page 25 · Harbourline Lending Fund · Information Memorandum</div>
  </section>

  <!-- Row 6 -->
  <section class="page">
    <div class="sub">8.4 Related party transactions</div>
    <div class="txt"><p>The Trustee may enter into transactions with related parties of the Manager on arm's length terms. All such transactions are recorded and reviewed by the Trustee.</p></div>
    <div class="sub">8.5 Privacy</div>
    <div class="txt"><p>Personal information collected on the application form is used to administer investments and meet legal obligations. Investors may request access to the information held about them.</p></div>
    <div class="sub">8.6 Anti-money laundering</div>
    <div class="txt"><p>The Trustee must verify the identity of every applicant before accepting an application, and may delay or refuse a transaction where it suspects a breach of the law.</p><p>Information may be reported to the relevant authorities where required.</p></div>
    <div class="pg-foot">Page 26 · Harbourline Lending Fund · Information Memorandum</div>
  </section>
  <section class="page">
    <div class="sub">8.7 Common Reporting Standard</div>
    <div class="txt"><p>The Trustee is required to collect information about the tax residency of investors and may report it to the tax office for exchange with other jurisdictions.</p></div>
    <div class="sub">8.8 Foreign Account Tax Compliance</div>
    <div class="txt"><p>The Fund must identify investors who are United States persons for tax purposes and report their holdings as required under the applicable agreement.</p></div>
    <div class="sub">8.9 Indemnification</div>
    <div class="txt"><p>The Trustee and Manager are indemnified out of the Fund's assets for liabilities properly incurred in performing their duties, except in cases of fraud, negligence or breach of trust.</p><p>Investors' liability is limited to the amount they have invested.</p></div>
    <div class="pg-foot">Page 27 · Harbourline Lending Fund · Information Memorandum</div>
  </section>
  <section class="page">
    <div class="sub">8.10 Amendments</div>
    <div class="txt"><p>The Trustee may amend the trust deed where it reasonably considers the change will not adversely affect investors' rights, or otherwise with the approval of a special resolution.</p></div>
    <div class="sub">8.11 Investor reports</div>
    <div class="txt"><p>Quarterly reports are sent to all investors covering loan performance, arrears, repayments and distributions. Audited accounts are provided annually.</p></div>
    <div class="sub">8.12 Questions and complaints</div>
    <div class="txt"><p>Questions about an investment should first be directed to the Manager. Complaints will be acknowledged promptly and responded to within thirty days.</p><p>If an investor is not satisfied, the complaint may be referred to the Trustee for review.</p></div>
    <div class="pg-foot">Page 28 · Harbourline Lending Fund · Information Memorandum</div>
  </section>
  <section class="page">
    <div class="pg-title"><span class="num">9</span>Application Process</div>
    <div class="txt">
      <p>To invest, complete the application form attached to this memorandum and provide certified identification documents and a wholesale investor certificate.</p>
      <p>Application monies should be paid by electronic transfer to the Fund's application account, quoting the investor's name as reference.</p>
      <p>Application monies are held in trust in a separate account until units are issued. Interest earned on application monies is retained by the Fund.</p>
      <p>The Trustee may accept or reject any application in whole or in part. If an application is rejected, the monies will be returned without interest.</p>
      <p>Investors will receive a confirmation statement once units have been issued.</p>
    </div>
    <div class="pg-foot">Page 29 · Harbourline Lending Fund · Information Memorandum</div>
  </section>
  <section class="page">
    <div class="pg-title"><span class="num">10</span>Glossary</div>
    <table class="tbl">
      <tr><td>Application</td><td>A request to subscribe for units in the Fund</td></tr>
      <tr><td>Borrower</td><td>A party to whom the Fund advances a loan</td></tr>
      <tr><td>Business Day</td><td>A weekday on which banks are open in Melbourne</td></tr>
      <tr><td>Fund</td><td>Harbourline Lending Fund</td></tr>
      <tr><td>Investor</td><td>A person who holds units in the Fund</td></tr>
      <tr><td>Loan</td><td>A secured commercial advance made by the Fund</td></tr>
      <tr><td>Manager</td><td>Halverton Asset Management Pty Ltd</td></tr>
      <tr><td>Trustee</td><td>Harbourline Trustee Services Pty Ltd</td></tr>
      <tr><td>Unit</td><td>An undivided interest in the Fund</td></tr>
      <tr><td>Valuation</td><td>An independent assessment of property value</td></tr>
    </table>
    <div class="pg-foot">Page 30 · Harbourline Lending Fund · Information Memorandum</div>
  </section>

  <!-- Row 7 -->
  <section class="page">
    <div class="pg-title"><span class="num">10</span>Glossary</div>
    <table class="tbl">
      <tr><td>Loan term</td><td>The agreed duration of each loan</td></tr>
      <tr><td>LVR</td><td>Loan to value ratio of the security property</td></tr>
      <tr><td>Project</td><td>A property secured by a loan from the Fund</td></tr>
      <tr><td>Wholesale</td><td>An investor who meets the legal wholesale tests</td></tr>
      <tr><td>Trust Deed</td><td>The constitution of the Fund, as amended</td></tr>
      <tr><td>Memorandum</td><td>This information memorandum</td></tr>
    </table>
    <div class="pg-foot">Page 31 · Harbourline Lending Fund · Information Memorandum</div>
  </section>
  <section class="page">
    <div class="pg-title"><span class="num">11</span>Corporate Directory</div>
    <table class="tbl">
      <tr><td>Trustee</td><td>Harbourline Trustee Services Pty Ltd, Level 9, 40 Quay Street</td></tr>
      <tr><td>Manager</td><td>Halverton Asset Management Pty Ltd, Level 12, 88 Market Lane</td></tr>
      <tr><td>Legal</td><td>Ashby Reid Lawyers</td></tr>
      <tr><td>Auditor</td><td>Coleman Price Partners</td></tr>
    </table>
    <div class="photo city" style="height:58px;margin-top:4px" role="img" aria-label="Glass towers reflecting blue sky"></div>
    <div class="pg-foot">Page 32 · Harbourline Lending Fund · Information Memorandum</div>
  </section>
</main>

<div class="signoff">
  <div class="brand"><span class="mark"></span>HALVERTON</div>
  <div class="im-line">IM for Harbourline Lending Fund</div>
</div>
</body>
</html>
```